Tolvik Commercial Cleaning is lookong for a new business card design.

A fresh new design that's professional and stylish. We need a serious upgrade to our business cards. I have included pictures of our existing ones. Our clients include professional individuals and business owners. We woupdblike something professional and upbeat. Please have fun and see what you come uo with.

Target Market(s)

Property managers, business owners, facility managers and other similar professionals

Industry/Entity Type

Janitorial

Contact Information for Business Card

Name, cell, office number, email, web address

Font styles to use
Sans Serif

Colors

Designer to choose colors to be used in the design.

Requirements
Must have
• please use the green color in our logo
Nice to have
• Bar code
Should not have
• Address

```html
<!DOCTYPE html>
<html lang="en">
<head>
<meta charset="utf-8">
<title>Tolvik Commercial Cleaning – Business Card</title>
<link rel="stylesheet" href="https://fonts.googleapis.com/css2?family=Montserrat:wght@400;500;600;700&display=swap">
<style>
  :root {
    --brand-green: #43ae57;
    --ink: #2b2b2b;
    --white: #ffffff;
    --backdrop: #e9e7e3;
    --card-shadow: rgba(0, 0, 0, 0.28);
  }
  * { margin: 0; padding: 0; box-sizing: border-box; }
  html, body {
    width: 900px; height: 1200px; overflow: hidden;
    background: var(--backdrop);
    font-family: "Montserrat", sans-serif;
  }
  .canvas { position: relative; width: 900px; height: 1200px; }

  .card {
    position: absolute; left: 80px; width: 742px; height: 440px;
    border-radius: 40px;
    box-shadow: 0 6px 14px var(--card-shadow);
    overflow: hidden;
  }
  .card--front { top: 132px; background: var(--white); }
  .card--back { top: 638px; background: var(--brand-green); }

  /* Front */
  .brand-name {
    position: absolute; right: 48px; top: 58px;
    text-align: right; color: var(--brand-green);
    font-weight: 700; line-height: 1.05;
  }
  .brand-name__main { display: block; font-size: 72px; letter-spacing: -1px; }
  .brand-name__sub { display: block; font-size: 18px; margin-top: 8px; }

  .holder { position: absolute; left: 42px; top: 270px; }
  .holder__name { color: var(--brand-green); font-size: 26px; font-weight: 700; }
  .holder__title { color: var(--ink); font-size: 16px; font-weight: 400; margin-top: 2px; }

  .divider {
    position: absolute; left: 42px; top: 330px;
    width: 653px; height: 2px; background: var(--brand-green);
  }

  .contacts { position: absolute; left: 42px; top: 342px; list-style: none; }
  .contacts__item {
    display: flex; align-items: center; gap: 10px;
    height: 22px; font-size: 16px; color: var(--ink);
  }
  .contacts__icon { width: 14px; height: 14px; fill: var(--brand-green); flex: none; }

  /* Back */
  .brand-name--reverse {
    position: absolute; left: 40px; top: 150px; width: 370px;
    text-align: center; color: var(--white);
    font-weight: 700; line-height: 1.05;
  }
  .brand-name--reverse .brand-name__main { font-size: 84px; }
  .brand-name--reverse .brand-name__sub { font-size: 21px; margin-top: 10px; }

  .rule-vertical {
    position: absolute; left: 408px; top: 146px;
    width: 2px; height: 182px; background: var(--white);
  }

  .services { position: absolute; left: 456px; top: 142px; color: var(--white); }
  .services__heading { font-size: 18px; font-weight: 600; margin-bottom: 6px; }
  .services__list { list-style: none; }
  .services__item {
    position: relative; padding-left: 14px;
    font-size: 16px; line-height: 19.7px; font-weight: 400;
  }
  .services__item::before {
    content: ""; position: absolute; left: 0; top: 8px;
    width: 6px; height: 6px; border-radius: 50%; background: var(--white);
  }
</style>
</head>
<body>
<main class="canvas">

  <section class="card card--front" aria-label="Business card front">
    <div class="brand-name">
      <span class="brand-name__main">Tolvik</span>
      <span class="brand-name__sub">Commercial Cleaning</span>
    </div>

    <div class="holder">
      <h1 class="holder__name">Maren Ostby</h1>
      <p class="holder__title">CEO &amp; Founder</p>
    </div>

    <div class="divider"></div>

    <ul class="contacts">
      <li class="contacts__item">
        <svg class="contacts__icon" viewBox="0 0 16 16" aria-hidden="true">
          <path d="M1 5c0-2 3-3 7-3s7 1 7 3v2h-3.5V5.5h-7V7H1zM3 8h10l1.5 6h-13z"/>
        </svg>
        (37) 555-0182
      </li>
      <li class="contacts__item">
        <svg class="contacts__icon" viewBox="0 0 16 16" aria-hidden="true">
          <path d="M1 3h14v10H1zM2.5 4.5 8 9l5.5-4.5z" fill-rule="evenodd"/>
        </svg>
        maren@tolvikcleaning.com
      </li>
      <li class="contacts__item">
        <svg class="contacts__icon" viewBox="0 0 16 16" aria-hidden="true">
          <circle cx="8" cy="8" r="7"/>
          <path d="M5 4c2 0 2 2 4 2s1 3-1 3-2 3-3 3-1-3-2-4 0-4 2-4z" fill="#ffffff"/>
        </svg>
        www.tolvikcleaning.com
      </li>
    </ul>
  </section>

  <section class="card card--back" aria-label="Business card back">
    <div class="brand-name brand-name--reverse">
      <span class="brand-name__main">Tolvik</span>
      <span class="brand-name__sub">Commercial Cleaning</span>
    </div>

    <div class="rule-vertical"></div>

    <div class="services">
      <h2 class="services__heading">OUR SERVICES</h2>
      <ul class="services__list">
        <li class="services__item">Carpet Cleaning</li>
        <li class="services__item">Construction Cleaning</li>
        <li class="services__item">Day Labor</li>
        <li class="services__item">Furniture Cleaning</li>
        <li class="services__item">Power Washing</li>
        <li class="services__item">VCT Cleaning</li>
        <li class="services__item">Window Cleaning</li>
        <li class="services__item">Furniture Cleaning</li>
      </ul>
    </div>
  </section>

</main>
</body>
</html>
```